Company web site

Looking for a full responsive(mobile friendly) wordpress implementation

Some material is in the website -- brelvanto.wordpress.com

But looking for a template more consistent with the logo design, and more future looking.

Target Market(s)

Enterprise Clients

Industry/Entity Type

It Company

Font styles to use
Sans Serif

Colors
33a6d7
0255a3
0455a3
cfdeed
85abd2
3176b5

Requirements
Must have
• about, contact information, partner page, success stories, customer testimonials. links to social presence.
• pricing information

```html
<!DOCTYPE html>
<html lang="en">
<head>
<meta charset="utf-8">
<title>Brelvanto — IoT Solutions</title>
<link href="https://fonts.googleapis.com/css2?family=Lora:wght@400;700&display=swap" rel="stylesheet">
<style>
:root{
  --sky:#33a6d7;
  --royal:#0255a3;
  --navy:#0455a3;
  --mist:#cfdeed;
  --steel:#85abd2;
  --mid:#3176b5;
  --ink:#444;
  --dark:#333333;
  --white:#ffffff;
}
*{box-sizing:border-box;margin:0;padding:0}
html,body{width:1200px;height:2922px;overflow:hidden}
body{position:relative;font-family:"Lora",Georgia,serif;color:var(--ink);background:var(--white)}
.abs{position:absolute}

/* header */
.site-header{top:0;left:0;width:1200px;height:88px;background:var(--white)}
.brand{left:98px;top:24px;display:flex;align-items:center;gap:8px}
.brand-dot{width:30px;height:30px;border-radius:50%;background:var(--sky)}
.brand-name{font-size:22px;font-weight:700;color:var(--sky)}
.main-nav{top:28px;left:470px;display:flex;align-items:center;gap:0;font-size:13px}
.main-nav a{color:var(--sky);text-decoration:none;text-transform:uppercase;margin-right:27px;line-height:32px}
.main-nav a.current{background:var(--sky);color:var(--white);padding:0 16px;border-radius:3px}

/* hero */
.hero{top:88px;left:0;width:1200px;height:536px;background:radial-gradient(ellipse at 75% 45%,#3d6a9e 0%,#1b3866 35%,#0c1d3e 75%,#08142c 100%)}
.hero-title{left:98px;top:178px;font-size:50px;font-weight:700;color:var(--white);letter-spacing:1px}
.hero-text{left:98px;top:250px;width:620px;font-size:24px;line-height:42px;color:var(--white)}
.btn{display:block;text-align:center;color:var(--white);font-size:13px;font-weight:700;text-transform:uppercase;border-radius:18px;line-height:35px}
.hero-btn{left:98px;top:362px;width:155px;background:var(--sky)}
.hero-arrow{top:248px}

/* welcome */
.welcome-title{left:98px;top:670px;font-size:26px;font-weight:700;color:var(--royal)}
.welcome-text{left:98px;top:730px;width:540px;font-size:12.5px;line-height:26px;color:#555}
.welcome-text p+p{margin-top:14px}
.welcome-btn{left:98px;top:886px;width:155px;background:var(--navy)}
.welcome-media{left:670px;top:680px;width:430px;height:238px;border:5px solid #f1f1f1;box-shadow:0 0 4px rgba(0,0,0,.15);background:linear-gradient(120deg,#cfd6dc 0%,#7e8d9a 40%,#2c3e50 75%,#1c2733 100%)}
.play{left:873px;top:775px;width:48px;height:48px;border-radius:50%;background:#111;border:2px solid #fff}

/* steps */
.steps-tab{left:0;top:978px;width:1200px;height:64px}
.steps-title{left:0;top:990px;width:1200px;text-align:center;font-size:25px;font-weight:700;color:var(--navy)}
.steps{left:0;top:1040px;width:1200px;height:368px;background:var(--sky)}
.step{top:1108px;width:300px;text-align:center;color:var(--white)}
.step-icon{width:112px;height:112px;border-radius:50%;background:var(--white);margin:0 auto;display:flex;align-items:center;justify-content:center}
.step-icon.is-dark{background:var(--navy)}
.step h3{font-size:13px;font-weight:700;line-height:26px;margin-top:28px}
.step p{font-size:12px;font-weight:700;line-height:25px;margin-top:20px}

/* testimonials */
.section-title{font-size:28px;font-weight:700;color:var(--navy)}
.testi-title{left:0;top:1460px;width:1200px;text-align:center}
.testi-box{left:133px;top:1543px;width:935px;height:200px;border:3px solid var(--navy)}
.avatar{left:203px;top:1581px;width:118px;height:118px;border-radius:50%;background:radial-gradient(circle at 50% 40%,#f2c9a8 0%,#d9534f 60%,#b23a36 100%)}
.quote-mark{left:355px;top:1583px}
.testi-text{left:410px;top:1622px;width:600px;font-size:12px;line-height:25px;color:#555}
.testi-name{left:760px;top:1685px;width:244px;text-align:right;font-size:13px;font-weight:700;color:var(--navy)}

/* feature band */
.feature{left:0;top:1806px;width:1200px;height:400px;background:linear-gradient(90deg,#8c7a6a 0%,#b3a396 30%,#a69a93 55%,#7d8389 80%,#6b7076 100%)}
.callout{left:400px;top:1874px}
.callout-text{left:515px;top:1950px;width:590px;text-align:center;font-size:12.5px;font-weight:700;line-height:24px;color:var(--white)}
.callout-name{left:800px;top:2008px;font-size:12.5px;font-weight:700;line-height:25px;color:var(--white)}

/* info columns */
.col-title{top:2256px;font-size:25px;font-weight:700;color:var(--navy)}
.partner-badge{left:100px;top:2312px;width:170px;height:72px;border:1px solid #bbb;background:#f4f4f4}
.partner-text{left:100px;top:2398px;width:240px;font-size:12px;line-height:25px;color:#666}
.blog-card{left:384px;top:2310px;width:284px;height:152px;border:1px solid #e3e3e3}
.blog-date{left:412px;top:2340px;font-size:13px;font-weight:700;color:var(--navy);display:flex;align-items:center;gap:8px}
.blog-text{left:412px;top:2370px;width:240px;font-size:12px;line-height:25px;color:#666}
.map{left:790px;top:2312px;width:310px;height:148px;background:linear-gradient(135deg,#eceae6 0%,#dcdad5 50%,#cfd3cf 100%)}
.contact-lines{left:792px;top:2470px;font-size:12px;line-height:26px;color:var(--navy)}

/* footer */
.site-footer{left:0;top:2590px;width:1200px;height:332px;background:var(--dark);color:var(--white)}
.footer-brand{left:0;top:2638px;width:1200px;display:flex;justify-content:center;align-items:center;gap:12px}
.footer-brand .brand-dot{width:44px;height:44px;background:var(--white)}
.footer-brand .brand-name{font-size:30px;color:var(--white)}
.footer-links-title{left:0;top:2726px;width:1200px;text-align:center;font-size:12px;font-weight:700;color:var(--white)}
.footer-links{left:0;top:2776px;width:1200px;display:flex;justify-content:center;font-size:12px;color:var(--white)}
.footer-links span{padding:0 30px}
.footer-links i{font-style:normal}
.footer-rule{left:100px;top:2836px;width:1000px;height:1px;background:#555}
.copyright{left:0;top:2866px;width:1200px;text-align:center;font-size:12px;color:var(--white)}
</style>
</head>
<body>

<header class="site-header abs">
  <div class="brand abs"><span class="brand-dot"></span><span class="brand-name">Brelvanto</span></div>
  <nav class="main-nav abs">
    <a class="current">Home</a><a>About</a><a>Partners</a><a>Pricing</a><a>Success Stories</a><a>Testimonials</a><a>Contact Us</a>
  </nav>
</header>

<section class="hero abs" role="img" aria-label="Hand holding a transparent smartphone over a dark blue technology backdrop"></section>
<h1 class="hero-title abs">BRELVANTO</h1>
<p class="hero-text abs">Brelvanto is company which provides specialized offerings in IoT domain</p>
<a class="btn hero-btn abs">Get Started</a>
<svg class="hero-arrow abs" style="left:40px" width="26" height="40" viewBox="0 0 26 40"><path d="M20 4 6 20l14 16" fill="none" stroke="#ccd" stroke-width="5"/></svg>
<svg class="hero-arrow abs" style="left:1128px" width="26" height="40" viewBox="0 0 26 40"><path d="M6 4l14 16L6 36" fill="none" stroke="#ccd" stroke-width="5"/></svg>

<h2 class="welcome-title abs">WELCOME TO BRELVANTO</h2>
<div class="welcome-text abs">
  <p>Brelvanto is company which provides specialized offerings in IoT domain. Based in the heart of the Silicon Valley, California. Brelvanto is built on decades of experience and knowledge</p>
  <p>Brelvanto CX IoT platform for OEM's is designed to ease the transition of Product companies from selling unconnected products, into providing service for connected devices.</p>
</div>
<a class="btn welcome-btn abs">Read More &gt;&gt;</a>
<div class="welcome-media abs" role="img" aria-label="Engineers working at computer monitors in an office"></div>
<svg class="play abs" viewBox="0 0 48 48"><path d="M19 14v20l15-10z" fill="#fff"/></svg>

<svg class="steps-tab abs" viewBox="0 0 1200 64"><path d="M272 62 310 2H890l38 60" fill="#fff" stroke="var(--sky)" stroke-width="3"/></svg>
<h2 class="steps-title abs">Simple Steps&nbsp; to take you to the next level</h2>
<section class="steps abs"></section>

<div class="step abs" style="left:102px">
  <div class="step-icon"><svg width="60" height="60" viewBox="0 0 60 60" fill="none" stroke="#0455a3" stroke-width="4"><circle cx="26" cy="26" r="18"/><path d="M39 39l14 14" stroke-linecap="round"/><path d="M17 31h18a5 5 0 0 0-1-10 7 7 0 0 0-13 1 4.5 4.5 0 0 0-4 9z" stroke-width="3"/></svg></div>
  <h3>Find a space for you<br>in the internet</h3>
  <p>Lorem ipsum dolor sit amet, &nbsp;elit. Vivamus orci, tempor ac felis et, gravida facilisis vitae. Donec et lectus ipsum.</p>
</div>
<div class="step abs" style="left:450px">
  <div class="step-icon is-dark"><svg width="60" height="60" viewBox="0 0 60 60" fill="none" stroke="#fff" stroke-width="4"><circle cx="18" cy="30" r="7"/><circle cx="42" cy="16" r="7"/><circle cx="42" cy="44" r="7"/><path d="M24 27l12-7M24 33l12 7"/></svg></div>
  <h3>Share your files<br>to anyone</h3>
  <p>Lorem ipsum dolor sit amet, &nbsp;elit. Vivamus orci, tempor ac felis et, gravida facilisis vitae. Donec et lectus ipsum.</p>
</div>
<div class="step abs" style="left:797px">
  <div class="step-icon"><svg width="62" height="60" viewBox="0 0 62 60" fill="none" stroke="#0455a3" stroke-width="4"><rect x="11" y="12" width="40" height="28" rx="2"/><path d="M5 46h52" stroke-linecap="round"/><path d="M31 18l8 3v6c0 5-4 8-8 9-4-1-8-4-8-9v-6z" fill="#0455a3" stroke-width="2"/></svg></div>
  <h3>Keep your website<br>safe and up to date</h3>
  <p>Lorem ipsum dolor sit amet, &nbsp;elit. Vivamus orci, tempor ac felis et, gravida facilisis vitae. Donec et lectus ipsum.</p>
</div>

<h2 class="section-title testi-title abs">Testimonials</h2>
<div class="testi-box abs"></div>
<div class="avatar abs" role="img" aria-label="Customer portrait"></div>
<svg class="quote-mark abs" width="38" height="30" viewBox="0 0 38 30" fill="#0455a3"><path d="M0 30V17C0 7 5 2 14 0v6c-4 1-6 4-6 8h6v16zM22 30V17c0-10 5-15 14-17v6c-4 1-6 4-6 8h6v16z"/></svg>
<p class="testi-text abs">Duis dignissim est odio, eleifend convallis diam sollicitudin ut. Proin ac feugiat felis, sit amet tincidunt erat Fusce pharetra neque ut pretium vestibulum. Donec condimentum tortor eget augue gravida malesuada.</p>
<p class="testi-name abs">- Scelerisque</p>

<section class="feature abs" role="img" aria-label="Smiling person giving a thumbs up, softly blurred"></section>
<svg class="callout abs" width="700" height="200" viewBox="0 0 700 200"><path d="M115 0H698V200H115V145L0 115 115 70z" fill="#33a6d7"/></svg>
<p class="callout-text abs">Duis dignissim est odio, eleifend convallis diam sollicitudin ut.Proin ac feugiat felis, sit amet tincidunt erat. Fusce onec condimentum tortor eget augue gravida malesuada</p>
<p class="callout-name abs">- Vestibulum Antey<br>&nbsp;&nbsp;Maecenas gravida vehicula</p>

<h2 class="col-title abs" style="left:100px">OUR PARTNER</h2>
<h2 class="col-title abs" style="left:386px">OUR BLOG POST</h2>
<h2 class="col-title abs" style="left:788px">CONTACT INFO</h2>

<div class="partner-badge abs"></div>
<p class="partner-text abs">Sed sit amet volutpat mauris, ut scelerisque dui. Duis a lorem vel eros iaculis lobortis a quis quam</p>

<div class="blog-card abs"></div>
<div class="blog-date abs"><svg width="13" height="13" viewBox="0 0 13 13" fill="#0455a3"><rect x="0" y="2" width="13" height="11" rx="1"/><rect x="2" y="5" width="9" height="6" fill="#fff"/><rect x="3" y="0" width="2" height="3"/><rect x="8" y="0" width="2" height="3"/></svg>July 1st, 2017</div>
<p class="blog-text abs">Duis dignissim est odio, eleifend convallis diam sollicitudin ut. Proin ac feugiat felis, sit amet tincidunt erat.</p>

<div class="map abs" role="img" aria-label="Street map showing the office location"></div>
<svg class="abs" style="left:932px;top:2330px" width="24" height="34" viewBox="0 0 24 34"><path d="M12 34C4 20 0 16 0 12a12 12 0 0 1 24 0c0 4-4 8-12 22z" fill="#d33"/><circle cx="12" cy="12" r="4" fill="#8a1c1c"/></svg>
<p class="contact-lines abs">+1-(555) 014-2290<br>418 Marlow Ave<br>Fernridge, CA 94000</p>

<footer class="site-footer abs"></footer>
<div class="footer-brand abs"><span class="brand-dot"></span><span class="brand-name">Brelvanto</span></div>
<p class="footer-links-title abs">- LINKS -</p>
<nav class="footer-links abs">
  <span>ABOUT</span><i>|</i><span>PARTNERS</span><i>|</i><span>PRICING</span><i>|</i><span>SUCCESS STORIES</span><i>|</i><span>TESTIMONIALS</span><i>|</i><span>CONTACT US</span>
</nav>
<div class="footer-rule abs"></div>
<p class="copyright abs">© Copyrights 2017 Brelvanto.Allrights Reserved</p>

</body>
</html>
```